Business Card Design

New business card design

Target Market(s)

Residential & Commercial Property Managers

Industry/Entity Type

Plumbing Services

Contact Information for Business Card

Name - Rowan Keddle, title - Director, Phone Number - 0431 286 517, email - rowan@tbk-plumbing.com.au, Company ABN - 73 215 904 386,

Font styles to use
Sans Serif

Colors
0054AA
0677BA
7BADD7
CADEEF
E8F1F8

```html
<!DOCTYPE html>
<html lang="en">
<head>
<meta charset="utf-8">
<title>TBK Plumbing Services – Business Card</title>
<link rel="stylesheet" href="https://fonts.googleapis.com/css2?family=Montserrat:wght@400;500;700&display=swap">
<style>
  :root {
    --stage: #2c2c2f;
    --card-front: #ffffff;
    --card-back: #111a23;
    --ink: #16191d;
    --ink-soft: #3a3d42;
    --accent: #1f9bd7;
    --rule: #6b6e73;
    --mark-back: #3c4855;
  }
  * { margin: 0; padding: 0; box-sizing: border-box; }
  html, body {
    width: 1200px; height: 800px; overflow: hidden;
    background: var(--stage);
    font-family: "Montserrat", Arial, sans-serif;
  }
  .canvas {
    position: relative; width: 1200px; height: 800px;
    display: flex; justify-content: center; align-items: center; gap: 60px;
  }
  .card {
    width: 330px; height: 540px; position: relative;
    box-shadow: 0 10px 30px rgba(0,0,0,.35);
  }
  .card--front { background: var(--card-front); color: var(--ink); text-align: center; }
  .card--back { background: var(--card-back); display: flex; align-items: center; justify-content: center; }

  .brand {
    display: flex; align-items: center; justify-content: center; gap: 8px;
    font-weight: 500; letter-spacing: .04em;
  }
  .brand__dot { width: 12px; height: 12px; border-radius: 50%; background: var(--accent); }
  .card--front .brand { position: absolute; top: 110px; left: 0; right: 0; font-size: 17px; color: var(--ink); }
  .card--back .brand { font-size: 17px; color: var(--mark-back); }

  .person { position: absolute; top: 250px; left: 0; right: 0; }
  .person__name { font-weight: 700; font-size: 24px; color: var(--accent); letter-spacing: .01em; }
  .person__title { font-weight: 500; font-size: 19px; color: var(--ink); margin-top: 2px; }

  .icon-row {
    position: absolute; top: 328px; left: 0; right: 0;
    display: flex; align-items: center; justify-content: center; gap: 6px;
  }
  .icon-row__line { width: 46px; height: 1px; background: var(--accent); margin: 0 6px; }
  .icon { width: 26px; height: 26px; border-radius: 6px; background: var(--accent); display: flex; align-items: center; justify-content: center; }
  .icon svg { width: 16px; height: 16px; }

  .contact { position: absolute; top: 376px; left: 0; right: 0; font-size: 13.5px; line-height: 1.45; color: var(--ink-soft); }
  .divider { position: absolute; top: 448px; left: 30px; right: 30px; height: 1px; background: var(--rule); }
  .abn { position: absolute; top: 460px; left: 0; right: 0; font-size: 13.5px; color: var(--ink-soft); }
</style>
</head>
<body>
<main class="canvas">
  <section class="card card--front" aria-label="Card front">
    <div class="brand"><span class="brand__dot"></span><span class="brand__name">TBK Plumbing Services</span></div>

    <div class="person">
      <p class="person__name">ROWAN KEDDLE</p>
      <p class="person__title">Director</p>
    </div>

    <div class="icon-row">
      <span class="icon-row__line"></span>
      <span class="icon" aria-label="Phone">
        <svg viewBox="0 0 16 16" fill="none" stroke="#fff" stroke-width="1.4" stroke-linecap="round" stroke-linejoin="round">
          <path d="M3 6c0-2 2-3 5-3s5 1 5 3l-2 .5-.5-1.5h-5L5 6.5z"/>
          <rect x="4" y="8" width="8" height="5" rx="1"/>
        </svg>
      </span>
      <span class="icon" aria-label="Email">
        <svg viewBox="0 0 16 16" fill="none" stroke="#fff" stroke-width="1.4" stroke-linejoin="round">
          <rect x="2" y="4" width="12" height="8" rx="1"/>
          <path d="M2 4l6 5 6-5"/>
        </svg>
      </span>
      <span class="icon" aria-label="Website">
        <svg viewBox="0 0 16 16" fill="none" stroke="#fff" stroke-width="1.3">
          <circle cx="8" cy="8" r="5.5"/>
          <path d="M2.5 8h11M8 2.5c2 2 2 9 0 11M8 2.5c-2 2-2 9 0 11"/>
        </svg>
      </span>
      <span class="icon-row__line"></span>
    </div>

    <div class="contact">
      <p>0431 286 517</p>
      <p>rowan@tbk-plumbing.com.au</p>
      <p>www.tbk-plumbing.com.au</p>
    </div>
    <div class="divider"></div>
    <p class="abn">ABN - 73 215 904 386</p>
  </section>

  <section class="card card--back" aria-label="Card back">
    <div class="brand"><span class="brand__dot"></span><span class="brand__name">TBK Plumbing Services</span></div>
  </section>
</main>
</body>
</html>
```